Business card for medical clinic

I need an upmarket, modern medical/health business card for my clinic

Contact Information for Business Card

name, address, email, qr code

```html
<!DOCTYPE html>
<html lang="en">
<head>
<meta charset="UTF-8">
<title>Meridian Care Clinic – Business Card</title>
<link rel="stylesheet" href="https://fonts.googleapis.com/css2?family=Cinzel:wght@500;600&family=Arimo:wght@400&display=swap">
<style>
  :root {
    --page-bg: #9a9a9a;
    --card-white: #fbfbfb;
    --brand-blue: #1f6fa3;
    --edge-blue: #2f97cf;
    --deep-blue: #0f5a85;
    --rule-blue: #6cb4dc;
    --text-grey: #4a4a4a;
    --icon-blue: #3aa3d8;
  }
  * { margin: 0; padding: 0; box-sizing: border-box; }
  html, body {
    width: 1200px; height: 1020px; overflow: hidden;
    background: var(--page-bg);
  }
  .canvas { position: relative; width: 1200px; height: 1020px; }

  .card {
    position: absolute;
    width: 700px; height: 400px;
    box-shadow: 0 14px 30px rgba(0,0,0,0.22);
  }

  /* Front */
  .card-front {
    left: 90px; top: 70px; background: var(--card-white);
    border-bottom: 6px solid var(--edge-blue);
  }
  .brand-front {
    position: absolute; right: 48px; top: 84px;
    font-family: "Cinzel", serif; font-weight: 600;
    font-size: 26px; letter-spacing: 0.5px; color: var(--brand-blue);
    white-space: nowrap;
  }
  .holder-name {
    position: absolute; left: 48px; top: 148px;
    font-family: "Cinzel", serif; font-weight: 600;
    font-size: 32px; letter-spacing: 1px; color: var(--brand-blue);
    white-space: nowrap;
  }
  .holder-title {
    position: absolute; left: 48px; top: 192px;
    font-family: "Arimo", sans-serif; font-size: 18px; color: var(--text-grey);
  }
  .divider {
    position: absolute; left: 48px; top: 226px;
    width: 560px; height: 1.5px; background: var(--rule-blue);
  }
  .contact-list {
    position: absolute; left: 48px; top: 244px; list-style: none;
    font-family: "Arimo", sans-serif; font-size: 18px; color: var(--text-grey);
  }
  .contact-list li { display: flex; align-items: center; gap: 10px; height: 32px; white-space: nowrap; }
  .contact-list svg { width: 14px; height: 14px; fill: var(--icon-blue); flex: none; }
  .address {
    position: absolute; right: 60px; bottom: 30px; text-align: right;
    font-family: "Arimo", sans-serif; font-style: normal;
    font-size: 18px; line-height: 1.35; color: var(--text-grey);
    white-space: nowrap;
  }

  /* Back */
  .card-back {
    left: 410px; top: 560px; background: var(--deep-blue);
    display: flex; align-items: center; justify-content: center;
  }
  .brand-back {
    font-family: "Cinzel", serif; font-weight: 600;
    font-size: 44px; letter-spacing: 1px; color: #ffffff;
    white-space: nowrap;
  }
</style>
</head>
<body>
<main class="canvas">

  <section class="card card-front" aria-label="Business card front">
    <div class="brand-front">Meridian Care Clinic</div>

    <h1 class="holder-name">DANIEL HARTWELL</h1>
    <p class="holder-title">Director/Founder</p>
    <div class="divider"></div>

    <ul class="contact-list">
      <li>
        <svg viewBox="0 0 16 16" aria-hidden="true"><path d="M3 1h3l1.5 4-2 1.3a9 9 0 0 0 4.2 4.2L11 8.5l4 1.5v3a2 2 0 0 1-2 2A12 12 0 0 1 1 3a2 2 0 0 1 2-2z"/></svg>
        04318 742 6093
      </li>
      <li>
        <svg viewBox="0 0 16 16" aria-hidden="true"><path d="M1 3h14v10H1zM2 4.2v.3l6 4.2 6-4.2v-.3z" fill-rule="evenodd"/></svg>
        info@meridiancareclinic.com
      </li>
      <li>
        <svg viewBox="0 0 16 16" aria-hidden="true"><circle cx="8" cy="8" r="7"/></svg>
        www.meridiancareclinic.com
      </li>
    </ul>

    <address class="address">
      1870 Harbor Lane<br>
      Westbrook AV 31827
    </address>
  </section>

  <section class="card card-back" aria-label="Business card back">
    <div class="brand-back">Meridian Care Clinic</div>
  </section>

</main>
</body>
</html>
```